Business Card for Field Lotus-Eco Friendly Organic Clothing Brand

We are looking for an amazing business card for our eco friendly, organic clothing brand. We are thinking maybe a business card with a peel off sticker on the back, since our hanging clothing tag is a peel off sticker on the back. I will attach our hang tag so we can make sure we stay in line with our design. I've also attached a bag we are doing because I do like the scattered emblem look as well.

```html
<!DOCTYPE html>
<html lang="en">
<head>
<meta charset="utf-8">
<title>Field Lotus – Business Card</title>
<link href="https://fonts.googleapis.com/css2?family=Lato:wght@400;700&display=swap" rel="stylesheet">
<style>
  :root {
    --page-bg: #ecebe8;
    --card-white: #ffffff;
    --olive-dark: #1a1f14;
    --gold: #cfa236;
    --gold-light: #f0d98a;
    --gold-deep: #b8892a;
    --text-light: #ffffff;
  }
  * { margin: 0; padding: 0; box-sizing: border-box; }
  html, body {
    width: 1200px; height: 900px; overflow: hidden;
    background: var(--page-bg);
    font-family: "Lato", sans-serif;
  }
  .canvas { position: relative; width: 1200px; height: 900px; }

  .card {
    position: absolute;
    box-shadow: 0 6px 18px rgba(0,0,0,0.18);
    overflow: hidden;
  }

  /* Front */
  .card-front {
    left: 78px; top: 35px; width: 588px; height: 363px;
    background: var(--card-white);
  }
  .card-front .bands { position: absolute; left: 0; top: 0; width: 588px; height: 363px; }
  .brand-mark {
    position: absolute; left: 0; right: 0; top: 62px;
    display: flex; flex-direction: column; align-items: center; gap: 8px;
  }
  .brand-row { display: flex; align-items: center; gap: 12px; }
  .brand-square { width: 22px; height: 22px; background: var(--gold); }
  .brand-name {
    font-weight: 700; font-size: 36px; color: var(--gold-deep);
    letter-spacing: 1px; line-height: 1;
  }
  .brand-url { font-size: 11px; color: var(--olive-dark); }

  .identity {
    position: absolute; right: 314px; top: 233px;
    text-align: right; color: var(--text-light);
  }
  .identity .name { font-size: 25px; font-weight: 400; line-height: 30px; }
  .identity .role { font-size: 17px; line-height: 22px; }
  .identity .address { font-size: 17px; line-height: 24px; margin-top: 7px; }

  .contacts {
    position: absolute; left: 312px; top: 237px;
    list-style: none; color: var(--text-light); font-size: 17px;
  }
  .contacts li { display: flex; align-items: center; gap: 8px; height: 24.5px; }
  .contacts svg { width: 16px; height: 16px; flex: none; }

  /* Back */
  .card-back {
    left: 388px; top: 505px; width: 567px; height: 352px;
    background: radial-gradient(circle at 262px 150px, #f6e6b0 0, #e9cd7c 90px, var(--gold) 200px, var(--gold) 100%);
  }
  .back-brand {
    position: absolute; left: 0; right: 42px; top: 118px;
    text-align: center; color: var(--text-light);
    font-weight: 700; font-size: 46px; line-height: 52px; letter-spacing: 2px;
  }
  .back-url {
    position: absolute; left: 0; right: 46px; top: 246px;
    text-align: center; color: var(--text-light); font-size: 17px;
  }
</style>
</head>
<body>
<main class="canvas">

  <section class="card card-front" aria-label="Card front">
    <svg class="bands" viewBox="0 0 588 363" width="588" height="363" aria-hidden="true">
      <defs>
        <linearGradient id="goldStripe" x1="0" y1="0" x2="0" y2="1">
          <stop offset="0" stop-color="#f0d98a"/>
          <stop offset="0.5" stop-color="#cfa236"/>
          <stop offset="1" stop-color="#a97c22"/>
        </linearGradient>
      </defs>
      <polygon points="0,187 398,187 380,212 0,212" fill="url(#goldStripe)"/>
      <polygon points="0,215 386,215 414,178 588,178 588,363 0,363" fill="#1a1f14"/>
    </svg>

    <div class="brand-mark">
      <div class="brand-row">
        <span class="brand-square"></span>
        <span class="brand-name">FIELD LOTUS</span>
      </div>
      <span class="brand-url">www.fieldlotus.com</span>
    </div>

    <div class="identity">
      <p class="name">John Smith</p>
      <p class="role">Managing Director</p>
      <p class="address">1234, Address GoesHere<br>Country, 12345</p>
    </div>

    <ul class="contacts">
      <li><svg viewBox="0 0 16 16"><rect width="16" height="16" rx="2" fill="#cfa236"/><path d="M4 5.5h8v5H4z" fill="none" stroke="#1a1f14" stroke-width="1.3"/><path d="M6 5.5V4h4v1.5" fill="none" stroke="#1a1f14" stroke-width="1.3"/></svg>123-456-7890</li>
      <li><svg viewBox="0 0 16 16"><rect width="16" height="16" rx="2" fill="#cfa236"/><rect x="5" y="3" width="6" height="10" rx="1" fill="none" stroke="#1a1f14" stroke-width="1.3"/></svg>123-456-7890</li>
      <li><svg viewBox="0 0 16 16"><rect width="16" height="16" rx="2" fill="#cfa236"/><rect x="3" y="4.5" width="10" height="7" fill="none" stroke="#1a1f14" stroke-width="1.2"/><path d="M3 4.5l5 4 5-4" fill="none" stroke="#1a1f14" stroke-width="1.2"/></svg>info@youremail.com</li>
      <li><svg viewBox="0 0 16 16"><rect width="16" height="16" rx="2" fill="#cfa236"/><path d="M5 11l6-6M7 5h4v4" fill="none" stroke="#1a1f14" stroke-width="1.4"/></svg>www.yourweb.com</li>
    </ul>
  </section>

  <section class="card card-back" aria-label="Card back">
    <p class="back-brand">FIELD<br>LOTUS</p>
    <p class="back-url">www.fieldlotus.com</p>
  </section>

</main>
</body>
</html>
```